Business card design Needed for new logo / Construction business, home extensions and new builds

We need a business card design using our new logo files which i will attach to this project :)

We are a small construction business specialising in home extensions, new builds and property development. We are very ambitious and would appreciate professional and elegant designs for our new business card.

Very serious about using the services on MakerQuarry and recently acquired our new logo from here :)

Please get involved, i will feedback when i can as i am very busy but can respond daily, thanks

Target Market(s)

People that want to build onto their houses, new building developments or adding too their existing property

Industry/Entity Type

Construction

Contact Information for Business Card

Renwick Tolliver Construction, Lionel Ashby (Managing Director), Tel 07822254961, email - info@renwick-tolliver, www.renwick-tolliver.co.uk

Colors

Designer to choose colors to be used in the design.

Requirements
Must have
• I like a deep grey on the back please. A lot of you have provided black from and back, try mixing things up a little. The black looks cool 😎 Thanks

```html
<!DOCTYPE html>
<html lang="en">
<head>
<meta charset="utf-8">
<title>Renwick Tolliver Construction – Business Card</title>
<link rel="stylesheet" href="https://fonts.googleapis.com/css2?family=Open+Sans:wght@400;600;700&display=swap">
<style>
  :root {
    --stage: #2b2b2f;
    --card-front: #1c1c20;
    --card-back: #3a3b41;
    --gold: #e0a92a;
    --gold-light: #f6d57f;
    --gold-deep: #b07a16;
    --silver: #c9ccd1;
    --silver-light: #f1f2f4;
    --text: #ffffff;
  }
  * { box-sizing: border-box; margin: 0; padding: 0; }
  html, body {
    width: 1200px; height: 780px; overflow: hidden;
    background: var(--stage);
    font-family: "Open Sans", Arial, sans-serif;
  }
  .canvas {
    position: relative; width: 1200px; height: 780px;
    display: flex; align-items: center; justify-content: center; gap: 44px;
  }
  .card {
    position: relative; width: 550px; height: 320px;
    border-radius: 22px;
    box-shadow: 0 4px 0 var(--gold), 0 18px 40px rgba(0,0,0,.45);
    overflow: hidden;
  }
  .card-front { background: var(--card-front); }
  .card-back { background: var(--card-back); }

  /* Brand name lockup */
  .brand { display: flex; align-items: center; gap: 14px; }
  .brand-mark { width: 22px; height: 22px; background: var(--gold); flex: none; }
  .brand-name {
    color: var(--silver);
    font-weight: 600;
    text-transform: uppercase;
    letter-spacing: .14em;
    line-height: 1.35;
  }

  /* Front */
  .card-front { display: flex; align-items: center; justify-content: center; }
  .card-front .brand-name { font-size: 22px; }

  /* Back */
  .card-back .brand { position: absolute; left: 36px; top: 96px; width: 216px; }
  .card-back .brand-name { font-size: 15px; }
  .divider {
    position: absolute; left: 270px; top: 48px;
    width: 2px; height: 200px; background: var(--text);
  }
  .contact { position: absolute; left: 296px; top: 44px; color: var(--text); }
  .person-name { font-size: 27px; font-weight: 700; line-height: 1.1; }
  .person-name .first { color: var(--silver); }
  .person-name .last { color: var(--gold); }
  .person-role { font-size: 12.5px; font-weight: 600; margin-top: 4px; }
  .address { font-size: 12.5px; line-height: 1.45; margin-top: 16px; }
  .details { list-style: none; margin-top: 16px; font-size: 12.5px; }
  .details li { display: flex; align-items: center; gap: 8px; line-height: 1.6; }
  .details svg { width: 12px; height: 12px; flex: none; }

  .edge-band {
    position: absolute; left: 0; right: 0; bottom: 18px; height: 16px;
    background: linear-gradient(90deg, var(--gold-deep) 0%, var(--gold-light) 30%, var(--gold) 55%, var(--silver) 62%, var(--silver-light) 80%, var(--silver) 100%);
  }
</style>
</head>
<body>
<main class="canvas">

  <section class="card card-front" aria-label="Card front">
    <div class="brand">
      <span class="brand-mark"></span>
      <span class="brand-name">Renwick Tolliver<br>Construction</span>
    </div>
  </section>

  <section class="card card-back" aria-label="Card back">
    <div class="brand">
      <span class="brand-mark"></span>
      <span class="brand-name">Renwick Tolliver Construction</span>
    </div>

    <span class="divider"></span>

    <div class="contact">
      <p class="person-name"><span class="first">Lionel</span> <span class="last">Ashby</span></p>
      <p class="person-role">Managing Director</p>
      <p class="address">Harlow Lane, Westbury<br>Kestonford, KT4 7RN</p>
      <ul class="details">
        <li>
          <svg viewBox="0 0 24 24" aria-hidden="true"><path fill="#e0a92a" d="M6.6 10.8a15.1 15.1 0 0 0 6.6 6.6l2.2-2.2c.3-.3.7-.4 1-.2 1.1.4 2.3.6 3.6.6.6 0 1 .4 1 1V20c0 .6-.4 1-1 1A17 17 0 0 1 3 4c0-.6.4-1 1-1h3.5c.6 0 1 .4 1 1 0 1.3.2 2.5.6 3.6.1.3 0 .7-.2 1z"/></svg>
          0782 225 4961
        </li>
        <li>
          <svg viewBox="0 0 24 24" aria-hidden="true"><path fill="#e0a92a" d="M3 5h18v14H3zM4.5 6.5 12 12l7.5-5.5v-.1h-15z"/></svg>
          info@renwick-tolliver.co.uk
        </li>
        <li>
          <svg viewBox="0 0 24 24" aria-hidden="true"><circle cx="12" cy="12" r="9" fill="none" stroke="#e0a92a" stroke-width="2"/><path d="M3 12h18M12 3c3 3 3 15 0 18M12 3c-3 3-3 15 0 18" fill="none" stroke="#e0a92a" stroke-width="1.6"/></svg>
          www.renwick-tolliver.co.uk
        </li>
      </ul>
    </div>

    <span class="edge-band"></span>
  </section>

</main>
</body>
</html>
```